Elevating our current Business Card Design

We want to elevate our current business card with a new design to look like a zenith 300 company. We are a premium lubricant distributor (oil and grease).
We need 2 versions, version 1 is as per the uploaded a copy of our current business card with the English version.
For our Chinese version we need to use the front to be English in English and have the back of the card designed exactly like the front for all info to be in Chinese.
The design template needs to be such that we can amend the template with adding different information for each person's card.
The background colour of the card can be changed- we just need to clearly see all information on the card and logos.
The QJR and Ember steady logos cannot have any colour or display changes- only use the logos attached.
All logos need to be included and all information from the attached current card

```html
<!DOCTYPE html>
<html lang="en">
<head>
<meta charset="utf-8">
<title>Norvane Lubricants – Business Card</title>
<link href="https://fonts.googleapis.com/css2?family=Open+Sans:ital,wght@0,400;0,600;0,700;1,700&display=swap" rel="stylesheet">
<style>
  :root {
    --stage: #222224;
    --card-white: #ffffff;
    --card-dark: #1e1e21;
    --brand-red: #e3261f;
    --brand-red-deep: #9e1a20;
    --brand-gold: #f0b528;
    --ink: #141414;
    --silver: #b9b9bd;
    --badge-orange: #f26a1b;
  }
  * { box-sizing: border-box; margin: 0; padding: 0; }
  html, body {
    width: 1200px; height: 780px; overflow: hidden;
    background: var(--stage);
    font-family: "Open Sans", Arial, sans-serif;
  }
  .canvas { position: relative; width: 1200px; height: 780px; }

  .card {
    position: absolute; top: 235px;
    width: 540px; height: 310px;
    border-radius: 3px; overflow: hidden;
    box-shadow: 0 18px 40px rgba(0,0,0,.55);
  }

  /* Front */
  .card-front { left: 40px; background: var(--card-white); }
  .card-front .swoosh { position: absolute; inset: 0; width: 100%; height: 100%; }

  .brand {
    position: absolute; display: flex; align-items: center; gap: 10px;
    font-weight: 700; color: var(--brand-red); letter-spacing: .5px;
  }
  .brand .brand-dot { border-radius: 50%; background: var(--brand-red); flex: none; }
  .card-front .brand { top: 34px; right: 36px; font-size: 26px; }
  .card-front .brand .brand-dot { width: 22px; height: 22px; }

  .person { position: absolute; left: 30px; top: 104px; }
  .person-name {
    font-size: 30px; font-weight: 700; font-style: italic;
    color: var(--brand-red); line-height: 1.1;
  }
  .person-title { font-size: 15px; font-weight: 400; color: var(--ink); margin-top: 4px; }

  .divider {
    position: absolute; left: 262px; top: 118px;
    width: 2px; height: 90px; background: var(--ink);
  }

  .contacts { position: absolute; left: 282px; top: 112px; list-style: none; }
  .contacts li {
    display: flex; align-items: center; gap: 9px;
    font-size: 14.5px; color: var(--ink); line-height: 20px;
  }
  .contacts svg { width: 13px; height: 13px; flex: none; }

  .address {
    position: absolute; left: 26px; bottom: 14px;
    font-size: 14px; color: var(--card-white);
  }

  /* Back */
  .card-back { left: 620px; background: var(--card-dark); }
  .card-back .brand {
    top: 86px; left: 0; right: 0; justify-content: center;
    font-size: 46px; gap: 16px;
  }
  .card-back .brand .brand-dot { width: 40px; height: 40px; }

  .partner-strip {
    position: absolute; left: 22px; right: 22px; bottom: 26px;
    display: flex; align-items: center; gap: 12px;
  }
  .badge-ring {
    width: 36px; height: 36px; border-radius: 50%;
    border: 3px solid var(--silver); background: var(--badge-orange);
    flex: none;
  }
  .badge-network {
    width: 54px; height: 36px; border-radius: 18px 18px 4px 4px;
    background: var(--card-white); flex: none;
  }
  .partner-distributor {
    display: flex; align-items: center; gap: 6px;
    height: 40px; padding: 0 12px;
    border: 2px solid var(--brand-red);
    font-size: 13px; font-weight: 700; color: var(--brand-red);
  }
  .partner-distributor .brand-dot { width: 10px; height: 10px; border-radius: 50%; background: var(--brand-red); }
  .badge-supplier {
    width: 120px; height: 40px; background: var(--brand-red); flex: none;
  }
</style>
</head>
<body>
<main class="canvas">

  <section class="card card-front" aria-label="Business card front">
    <svg class="swoosh" viewBox="0 0 540 310" preserveAspectRatio="none" aria-hidden="true">
      <defs>
        <linearGradient id="redBand" x1="0" y1="0" x2="1" y2="0">
          <stop offset="0" stop-color="var(--brand-red-deep)"/>
          <stop offset=".55" stop-color="var(--brand-red)"/>
          <stop offset="1" stop-color="var(--brand-red)"/>
        </linearGradient>
      </defs>
      <path d="M0,200 Q230,292 540,292 L540,310 L0,310 Z" fill="url(#redBand)"/>
      <path d="M0,186 Q240,280 520,282" fill="none" stroke="var(--brand-gold)" stroke-width="3"/>
    </svg>

    <div class="brand"><span class="brand-dot"></span>Norvane</div>

    <div class="person">
      <p class="person-name">Maren Holt</p>
      <p class="person-title">Administration Executive</p>
    </div>

    <div class="divider"></div>

    <ul class="contacts">
      <li>
        <svg viewBox="0 0 16 16" aria-hidden="true"><path fill="var(--brand-red)" d="M3 1l3 3-2 2c1 2 3 4 5 5l2-2 3 3-2 3C6 15 1 10 1 3z"/></svg>
        1300 412 706
      </li>
      <li>
        <svg viewBox="0 0 16 16" aria-hidden="true"><rect x="4" y="1" width="8" height="14" rx="1.5" fill="none" stroke="var(--brand-red)" stroke-width="1.8"/></svg>
        +61 400 218 947
      </li>
      <li>
        <svg viewBox="0 0 16 16" aria-hidden="true"><rect x="1" y="6" width="14" height="9" rx="1" fill="var(--brand-red)"/><rect x="4" y="1" width="8" height="6" fill="none" stroke="var(--brand-red)" stroke-width="1.5"/></svg>
        +61 8 9000 4521
      </li>
      <li>
        <svg viewBox="0 0 16 16" aria-hidden="true"><circle cx="8" cy="8" r="6.5" fill="none" stroke="var(--brand-red)" stroke-width="1.6"/><path d="M1.5 8h13M8 1.5c-3 3-3 10 0 13M8 1.5c3 3 3 10 0 13" fill="none" stroke="var(--brand-red)" stroke-width="1.2"/></svg>
        www.norvanedirect.com
      </li>
      <li>
        <svg viewBox="0 0 16 16" aria-hidden="true"><rect x="1" y="3" width="14" height="10" rx="1" fill="var(--brand-red)"/><path d="M1.5 3.5L8 9l6.5-5.5" fill="none" stroke="#fff" stroke-width="1.3"/></svg>
        maren.holt@norvanedirect.com
      </li>
    </ul>

    <p class="address">14 Freight Way Eastfield, WA 6000</p>
  </section>

  <section class="card card-back" aria-label="Business card back">
    <div class="brand"><span class="brand-dot"></span>Norvane</div>

    <div class="partner-strip">
      <div class="badge-network" role="img" aria-label="Ember steady network member badge"></div>
      <div class="badge-ring" role="img" aria-label="QJR certification badge"></div>
      <div class="partner-distributor"><span class="brand-dot"></span>Norvane Lubricants</div>
      <div class="badge-supplier" role="img" aria-label="Premium lubricants supplier badge"></div>
      <div class="badge-ring" role="img" aria-label="QJR certification badge"></div>
      <div class="badge-ring" role="img" aria-label="QJR certification badge"></div>
    </div>
  </section>

</main>
</body>
</html>
```